Gobal construction supply company needs new business card design

I need a business card design for my global supply company using an existing logo. i will be looking to print these on rounded corner cards with the black background version of my logo on the back. on the front white background, my logo again and my simple details.

```html
<!DOCTYPE html>
<html lang="en">
<head>
<meta charset="utf-8">
<title>Meridian Build Supply – Business Cards</title>
<link rel="stylesheet" href="https://fonts.googleapis.com/css2?family=Montserrat:wght@700&family=Roboto:wght@400;500&display=swap">
<style>
  :root {
    --bg: #3a3a3c;
    --black: #0c0c0c;
    --back-black: #141414;
    --emboss: #2c2c2c;
    --white: #ffffff;
    --red: #d7111b;
    --ink: #1a1a1a;
    --muted: #555555;
  }
  * { box-sizing: border-box; margin: 0; padding: 0; }
  html, body { width: 1200px; height: 1000px; overflow: hidden; }
  body {
    background: var(--bg);
    font-family: "Roboto", Arial, sans-serif;
    position: relative;
  }
  .card {
    position: absolute;
    left: 250px;
    width: 700px;
    height: 400px;
    border-radius: 34px;
    overflow: hidden;
  }

  /* Company name, set as plain text */
  .company-name {
    position: absolute;
    left: 0; right: 0;
    text-align: center;
    font-family: "Montserrat", Arial, sans-serif;
    font-weight: 700;
    font-size: 36px;
    letter-spacing: 1px;
    white-space: nowrap;
  }

  /* Back */
  .card-back { top: 70px; background: var(--back-black); }
  .card-back .company-name { top: 178px; color: var(--emboss); }

  /* Front */
  .card-front { top: 530px; background: var(--white); }
  .front-band { position: absolute; left: 0; top: 0; width: 100%; height: 190px; background: var(--black); }
  .front-rule { position: absolute; left: 0; top: 190px; width: 100%; height: 6px; background: var(--red); }
  .card-front .company-name { top: 72px; color: var(--white); }

  .person { position: absolute; top: 218px; left: 0; right: 0; text-align: center; }
  .person-name {
    font-family: "Montserrat", Arial, sans-serif;
    font-weight: 700; font-size: 25px; color: var(--red); letter-spacing: 0.5px;
  }
  .person-title { font-size: 12px; font-weight: 500; color: var(--ink); letter-spacing: 0.5px; margin-top: 2px; }

  .contacts {
    position: absolute; top: 290px; left: 0; right: 0;
    display: flex; justify-content: center; gap: 22px;
    font-size: 16px; color: var(--ink); line-height: 25px;
  }
  .contact-address { text-align: right; }
  .contact-divider { width: 1.5px; background: var(--muted); }
  .contact-line { display: flex; align-items: center; gap: 8px; }
  .contact-address .contact-line { justify-content: flex-end; }
  .icon { width: 13px; height: 13px; fill: var(--red); flex: none; }
  .web-accent { color: var(--red); font-weight: 500; }
</style>
</head>
<body>

<section class="card card-back" aria-label="Card back">
  <div class="company-name">MERIDIAN BUILD SUPPLY</div>
</section>

<section class="card card-front" aria-label="Card front">
  <div class="front-band"></div>
  <div class="front-rule"></div>

  <div class="company-name">MERIDIAN BUILD SUPPLY</div>

  <div class="person">
    <div class="person-name">DANIEL MARSH</div>
    <div class="person-title">MANAGING DIRECTOR</div>
  </div>

  <div class="contacts">
    <div class="contact-address">
      <div class="contact-line"><span>48 Harbour Road</span></div>
      <div class="contact-line"><span>Kestrel Bay, QL 4021</span></div>
      <div class="contact-line">
        <svg class="icon" viewBox="0 0 24 24" aria-hidden="true"><path d="M6.6 10.8a15.1 15.1 0 0 0 6.6 6.6l2.2-2.2a1 1 0 0 1 1-.25 11.4 11.4 0 0 0 3.6.57 1 1 0 0 1 1 1V20a1 1 0 0 1-1 1A17 17 0 0 1 3 4a1 1 0 0 1 1-1h3.5a1 1 0 0 1 1 1c0 1.25.2 2.45.57 3.57a1 1 0 0 1-.25 1z"/></svg>
        <span>+1 (555) 014 2290</span>
      </div>
    </div>
    <div class="contact-divider"></div>
    <div class="contact-details">
      <div class="contact-line">
        <svg class="icon" viewBox="0 0 24 24" aria-hidden="true"><path d="M7 1h10a2 2 0 0 1 2 2v18a2 2 0 0 1-2 2H7a2 2 0 0 1-2-2V3a2 2 0 0 1 2-2zm0 3v14h10V4z"/></svg>
        <span>+1 (555) 014 2290</span>
      </div>
      <div class="contact-line">
        <svg class="icon" viewBox="0 0 24 24" aria-hidden="true"><path d="M2 5h20v14H2zm2 2v.5l8 5 8-5V7l-8 5z"/></svg>
        <span>dan@meridianbuild.com</span>
      </div>
      <div class="contact-line">
        <svg class="icon" viewBox="0 0 24 24" aria-hidden="true"><path d="M12 2a10 10 0 1 0 0 20 10 10 0 0 0 0-20zm-1 17.9A8 8 0 0 1 4.1 13H7c.2 2.6 1.6 5 4 6.9zM4.1 11A8 8 0 0 1 11 4.1C8.6 6 7.2 8.4 7 11zm4.9 0c.2-2.4 1.2-4.5 3-6.3 1.8 1.8 2.8 3.9 3 6.3zm0 2h6c-.2 2.4-1.2 4.5-3 6.3-1.8-1.8-2.8-3.9-3-6.3zm4 6.9c2.4-1.9 3.8-4.3 4-6.9h2.9a8 8 0 0 1-6.9 6.9zM17 11c-.2-2.6-1.6-5-4-6.9a8 8 0 0 1 6.9 6.9z"/></svg>
        <span>www.<span class="web-accent">meridianbuild</span>.com</span>
      </div>
    </div>
  </div>
</section>

</body>
</html>
```